Commercial painting contractor in need of graphic designs for new trade show booth.

Brellow Industries, Inc. is a leading commercial and multifamily painter in Texas for new construction interested in growing its repaint business. We will be attending the Pellwyn Rental Housing Guild Expo in October and are looking to finalize our booth design and get it ordered by 8/15. The booth layout is selected, and we have a logo and basic brand board. We are looking for graphic design that we can use for the next 3+ years without appearing dated. We are considering incorporating more of the baby blue color into our repaint branding (see bi-logo-dark blued-bg attached). The blue and white logo is our standard.
BrellowInd website: www.coatsbrellow.example
Trade Show booth website: https://fieldkioskframes.example/10X10-Custom-Trade-Show-Display-Booth-I
Look and feel
Each slider illustrates characteristics of the customer's brand and the style your logo design should communicate.

```html
<!DOCTYPE html>
<html lang="en">
<head>
<meta charset="utf-8">
<title>Brellow Industries, Inc. — Booth Graphics</title>
<link rel="stylesheet" href="https://fonts.googleapis.com/css2?family=Arimo:wght@700&family=Libre+Baskerville:ital@1&family=Montserrat:wght@700&family=Raleway:wght@400&display=swap">
<style>
  :root{
    --royal:#1530b0;
    --royal-deep:#0f2390;
    --lavender:#dfe3fa;
    --lavender-mid:#c9cff2;
    --white:#ffffff;
    --ink:#1c1c24;
    --screen:#2f3447;
    --shelf:#3a3f55;
    --page:#eef0f4;
  }
  *{box-sizing:border-box;margin:0;padding:0}
  html,body{width:1200px;height:1200px;overflow:hidden;background:var(--page)}
  .sheet{position:relative;width:1200px;height:1200px}
  .brand-name{font-family:"Arimo",Arial,sans-serif;font-weight:700;letter-spacing:.5px;text-transform:uppercase;text-align:center}
  .since-script{font-family:"Libre Baskerville",Georgia,serif;font-style:italic;text-align:center;letter-spacing:1px}
  .since-tag{font-family:"Raleway",sans-serif;font-weight:400;text-align:center}
  .web{font-family:"Montserrat",sans-serif;font-weight:700;text-align:center}
  .mark{display:flex;flex-direction:column;align-items:center;gap:6px;position:absolute;left:0;right:0}
  .mark-dot{border-radius:50%;flex:none}

  /* Tower */
  .tower{position:absolute;left:40px;top:60px;width:290px;height:1080px}
  .tower-shape{position:absolute;inset:0}
  .tower .mark-dot{width:46px;height:46px;background:var(--royal)}
  .tower .brand-name{color:var(--royal-deep);font-size:15px}
  .tower .since-script{color:var(--royal-deep);font-size:12px}
  .tower-screen{position:absolute;left:30px;top:340px;width:230px;height:140px;background:var(--screen);border:4px solid var(--ink)}
  .tower-shelf{position:absolute;left:12px;width:266px;height:14px;background:var(--shelf);border-radius:2px}

  /* Backwall */
  .backwall{position:absolute;left:360px;top:60px;width:800px;height:590px;background:var(--royal);border-radius:22px 22px 0 0;overflow:hidden}
  .backwall-photo{position:absolute;inset:0;background:linear-gradient(160deg,#2a46c4 0%,#1934b4 45%,#122a9c 100%)}
  .backwall .mark{top:70px}
  .backwall .mark-dot{width:90px;height:90px;background:var(--white)}
  .backwall .brand-name{color:var(--white);font-size:23px}
  .backwall .since-script{color:var(--white);font-size:16px}
  .backwall-stroke{position:absolute;left:0;top:260px}
  .backwall-since{position:absolute;left:340px;top:318px;color:var(--royal);font-size:52px}
  .roller{position:absolute;left:690px;top:290px;width:40px;height:130px;background:#2a3fa8;border-radius:8px}
  .backwall-contact{position:absolute;left:0;right:0;bottom:30px;color:var(--white);text-align:center}
  .backwall-phone{display:flex;justify-content:center;align-items:center;gap:12px;font-family:"Montserrat",sans-serif;font-weight:700;font-size:30px}
  .backwall .web{font-size:24px;margin-top:8px}

  /* Kiosk */
  .kiosk{position:absolute;left:380px;top:690px;width:220px;height:450px;background:var(--royal);border-radius:40px 40px 6px 6px;overflow:hidden}
  .kiosk-top{position:absolute;top:14px;left:0;right:0;display:flex;justify-content:center;align-items:center;gap:6px;color:var(--white)}
  .kiosk .kiosk-top .mark-dot{width:12px;height:12px;background:var(--white)}
  .kiosk .kiosk-top .brand-name{font-size:7px}
  .kiosk-screen{position:absolute;left:40px;top:40px;width:140px;height:56px;background:#050d2e;border-radius:3px}
  .kiosk .mark{top:130px}
  .kiosk .mark .mark-dot{width:44px;height:44px;background:var(--white)}
  .kiosk .mark .brand-name{color:var(--white);font-size:10px}
  .kiosk-band{position:absolute;left:0;top:255px}
  .kiosk-since{position:absolute;left:0;right:0;top:280px;color:var(--royal);font-size:22px}
  .kiosk-contact{position:absolute;left:0;right:0;bottom:30px;color:var(--white)}
  .kiosk-phone{font-family:"Montserrat",sans-serif;font-weight:700;font-size:17px;text-align:center}
  .kiosk .web{font-size:9px;margin-top:8px}

  /* Counter */
  .counter{position:absolute;left:640px;top:690px;width:520px;height:450px;background:var(--royal);border-radius:4px;overflow:hidden}
  .counter .mark{top:80px}
  .counter .mark-dot{width:80px;height:80px;background:var(--white)}
  .counter .brand-name{color:var(--white);font-size:19px}
  .counter .since-script{color:var(--white);font-size:14px}
  .counter-band{position:absolute;left:0;bottom:0}
  .counter .web{position:absolute;left:0;right:0;bottom:55px;color:var(--ink);font-size:27px}
</style>
</head>
<body>
<main class="sheet">

  <section class="tower" aria-label="Tower display graphic">
    <svg class="tower-shape" width="290" height="1080" viewBox="0 0 290 1080">
      <defs>
        <linearGradient id="towerFill" x1="0" y1="0" x2="0" y2="1">
          <stop offset="0" stop-color="#e4e7fb"/>
          <stop offset="1" stop-color="#c9cff2"/>
        </linearGradient>
      </defs>
      <path d="M0 120 Q145 -40 290 120 Q290 200 262 300 L262 1080 L28 1080 L28 300 Q0 200 0 120 Z" fill="url(#towerFill)"/>
    </svg>
    <div class="mark" style="top:80px">
      <span class="mark-dot"></span>
      <span class="brand-name">Brellow Industries, Inc.</span>
      <span class="since-script">Since 1972</span>
    </div>
    <div class="tower-screen"></div>
    <div class="tower-shelf" style="top:560px"></div>
    <div class="tower-shelf" style="top:680px"></div>
    <div class="mark" style="top:800px">
      <span class="mark-dot"></span>
      <span class="brand-name">Brellow Industries, Inc.</span>
    </div>
  </section>

  <section class="backwall" aria-label="Backwall graphic">
    <div class="backwall-photo" role="img" aria-label="Blue-toned photograph of a multifamily apartment building with trees"></div>
    <div class="mark">
      <span class="mark-dot"></span>
      <span class="brand-name">Brellow Industries, Inc.</span>
      <span class="since-script">Since 1972</span>
    </div>
    <svg class="backwall-stroke" width="800" height="240" viewBox="0 0 800 240">
      <path d="M0 230 Q140 120 330 60 Q520 10 700 30 L700 150 Q520 160 360 180 Q160 210 0 240 Z" fill="#ffffff" opacity=".96"/>
    </svg>
    <div class="since-tag backwall-since">Since 1972</div>
    <div class="roller" role="img" aria-label="Paint roller finishing the brush stroke"></div>
    <div class="backwall-contact">
      <div class="backwall-phone">
        <svg width="30" height="30" viewBox="0 0 24 24" aria-hidden="true"><path fill="#fff" d="M6.6 10.8a15.1 15.1 0 0 0 6.6 6.6l2.2-2.2a1 1 0 0 1 1-.25 11.4 11.4 0 0 0 3.6.57 1 1 0 0 1 1 1V20a1 1 0 0 1-1 1A17 17 0 0 1 3 4a1 1 0 0 1 1-1h3.5a1 1 0 0 1 1 1c0 1.250.2 2.450.57 3.570a1 1 0 0 1-.25 1z"/></svg>
        <span>555-013-4470</span>
      </div>
      <div class="web">www.coatsbrellow.example</div>
    </div>
  </section>

  <section class="kiosk" aria-label="Kiosk graphic">
    <div class="kiosk-top">
      <span class="mark-dot"></span>
      <span class="brand-name">Brellow Industries, Inc.</span>
    </div>
    <div class="kiosk-screen"></div>
    <div class="mark">
      <span class="mark-dot"></span>
      <span class="brand-name">Brellow Industries, Inc.</span>
    </div>
    <svg class="kiosk-band" width="220" height="110" viewBox="0 0 220 110">
      <path d="M0 16 Q110 0 220 4 L220 70 Q110 76 0 108 Z" fill="#ffffff"/>
    </svg>
    <div class="since-tag kiosk-since">Since 1972</div>
    <div class="kiosk-contact">
      <div class="kiosk-phone">555-013-4470</div>
      <div class="web">www.coatsbrellow.example</div>
    </div>
  </section>

  <section class="counter" aria-label="Counter graphic">
    <div class="mark">
      <span class="mark-dot"></span>
      <span class="brand-name">Brellow Industries, Inc.</span>
      <span class="since-script">Since 1972</span>
    </div>
    <svg class="counter-band" width="520" height="170" viewBox="0 0 520 170">
      <path d="M0 70 Q260 -10 520 12 L520 170 L0 170 Z" fill="#ffffff"/>
    </svg>
    <div class="web">www.coatsbrellow.example</div>
  </section>

</main>
</body>
</html>
```